Need help in designing new business card utilizing our new logo.

BuildMark Solutions works with Construction Business Owners, Managers & IT Professionals to strengthen software usage and increase user productivity.

Our Construction Accounting and Mobile Field Management Software Clients engage with us in the following areas:

New Software Implementations
Software Re-Implementations
Redesigning Software Usage at the User Level
Project Coordination & Management
Continued Software Support

Old tag line:
Weighing Options - Implementing Solutions

www.buildmark-solutions.example

Ridge 4 is a product, but not needed for a new business card.

```html
<!DOCTYPE html>
<html lang="en">
<head>
<meta charset="utf-8">
<title>BuildMark Solutions – Business Card</title>
<link href="https://fonts.googleapis.com/css2?family=Montserrat:wght@500;600&family=Open+Sans:wght@400;600&display=swap" rel="stylesheet">
<style>
  :root {
    --brand-blue: #26309a;
    --brand-blue-deep: #1c2585;
    --silver: #b9bcc4;
    --silver-light: #e4e5e9;
    --card-white: #ffffff;
    --text-grey: #4a4a50;
    --back-text: #d6d9ee;
    --page-bg: #d9dbe0;
  }
  * { margin: 0; padding: 0; box-sizing: border-box; }
  html, body { width: 1200px; height: 900px; overflow: hidden; }
  body {
    background: var(--page-bg);
    font-family: "Open Sans", sans-serif;
    position: relative;
  }
  .card {
    position: absolute;
    left: 285px;
    width: 630px;
    height: 360px;
    border-radius: 18px;
    overflow: hidden;
  }
  .card-front { top: 60px; background: linear-gradient(160deg, #ffffff 0%, #f1f2f4 100%); }
  .card-back { top: 480px; background: linear-gradient(150deg, var(--brand-blue) 0%, var(--brand-blue-deep) 100%); }

  .front-wave { position: absolute; inset: 0; width: 100%; height: 100%; }

  .brand-block { position: absolute; left: 44px; top: 62px; }
  .brand-name {
    font-family: "Montserrat", sans-serif;
    font-weight: 600;
    font-size: 26px;
    color: var(--brand-blue);
    display: flex; align-items: center; gap: 10px;
    letter-spacing: 0.5px;
  }
  .brand-square { width: 18px; height: 18px; background: var(--brand-blue); }
  .tagline {
    margin-top: 16px;
    font-family: "Montserrat", sans-serif;
    font-weight: 500;
    font-size: 15px;
    line-height: 1.35;
    color: var(--brand-blue);
  }

  .divider {
    position: absolute; left: 318px; top: 118px;
    width: 1.5px; height: 150px; background: var(--brand-blue);
  }

  .contact-block { position: absolute; left: 338px; top: 110px; }
  .person-name {
    font-family: "Montserrat", sans-serif;
    font-weight: 600; font-size: 24px; color: var(--brand-blue);
  }
  .person-role { font-size: 14px; color: var(--text-grey); margin-bottom: 10px; }
  .contact-list { list-style: none; }
  .contact-list li {
    display: flex; align-items: center; gap: 8px;
    font-size: 12.5px; line-height: 1.55; color: var(--text-grey);
  }
  .contact-list svg { width: 11px; height: 11px; fill: var(--brand-blue); flex: none; }
  .address { margin-top: 4px; font-size: 12.5px; line-height: 1.55; color: var(--text-grey); }

  .back-brand {
    position: absolute; left: 0; right: 0; top: 88px;
    display: flex; justify-content: center; align-items: center; gap: 12px;
    font-family: "Montserrat", sans-serif; font-weight: 600; font-size: 34px;
    color: var(--card-white); letter-spacing: 0.5px;
  }
  .back-brand .brand-square { width: 24px; height: 24px; background: var(--card-white); }
  .service-list {
    position: absolute; left: 0; right: 0; top: 170px;
    list-style: none; text-align: center;
    font-family: "Montserrat", sans-serif; font-weight: 500;
    font-size: 15px; line-height: 1.6; color: var(--back-text);
  }
</style>
</head>
<body>

<section class="card card-front">
  <svg class="front-wave" viewBox="0 0 630 360" preserveAspectRatio="none" aria-hidden="true">
    <path d="M0 210 C120 230 230 270 300 330 C320 348 335 356 345 360 L0 360 Z" fill="var(--silver)"/>
    <path d="M0 222 C115 244 220 282 285 340 C300 352 312 358 320 360 L0 360 Z" fill="var(--brand-blue)"/>
    <path d="M0 205 C125 224 240 262 310 322" stroke="var(--silver-light)" stroke-width="3" fill="none"/>
  </svg>

  <div class="brand-block">
    <div class="brand-name"><span class="brand-square"></span>BuildMark Solutions</div>
    <p class="tagline">Construction Accounting<br>Software Consultants</p>
  </div>

  <div class="divider"></div>

  <div class="contact-block">
    <h1 class="person-name">Dana R. Whitfield</h1>
    <p class="person-role">Owner</p>
    <ul class="contact-list">
      <li><svg viewBox="0 0 12 12"><path d="M2 1h3l1 3-1.5 1a7 7 0 0 0 2.5 2.5L8 6l3 1v3c0 .6-.4 1-1 1C5 11 1 7 1 2c0-.6.4-1 1-1z"/></svg>800-555-0142 ext.100</li>
      <li><svg viewBox="0 0 12 12"><path d="M3 0h6a1 1 0 0 1 1 1v10a1 1 0 0 1-1 1H3a1 1 0 0 1-1-1V1a1 1 0 0 1 1-1zm0 1.5v7.5h6V1.5z"/></svg>518-555-0193</li>
      <li><svg viewBox="0 0 12 12"><path d="M0 2h12v8H0zm1.2 1.2v.3L6 6.6l4.8-3.1v-.3zM1.2 5v3.8h9.6V5L6 8z"/></svg>dana.whitfield@buildmark-solutions.example</li>
      <li><svg viewBox="0 0 12 12"><circle cx="6" cy="6" r="5.5"/></svg>www.buildmark-solutions.example</li>
    </ul>
    <p class="address">14 Maple Row - Box 118<br>Brookfield NY 12000</p>
  </div>
</section>

<section class="card card-back">
  <div class="back-brand"><span class="brand-square"></span>BuildMark Solutions</div>
  <ul class="service-list">
    <li>New Software Implementations | Software Re-Implementations</li>
    <li>Redesigning Software Usage at the User Level</li>
    <li>Project Coordination &amp; Management</li>
    <li>Continued Software Support</li>
  </ul>
</section>

</body>
</html>
```